Local fast-growing company in the service sector

We are looking for a modern business card design, which should also appear on our letterheads

Target Market(s)

Private and industrial sectors

Contact Information for Business Card

Vorname Name
Kellberger Str. 18
74286 Oberweiler
Tel.: 07146-839214-0
Name@agentur-kvtl.de

Colors
9d9d9d
919191
aaaaaa

Requirements
Must have
• The logo (file) in silver

```html
<!DOCTYPE html>
<html lang="de">
<head>
<meta charset="utf-8">
<title>KVTL – Visitenkarte</title>
<link rel="stylesheet" href="https://fonts.googleapis.com/css2?family=Lato:wght@400;700;900&display=swap">
<style>
  :root {
    --page-bg: #e6e6e6;
    --card-light: #ffffff;
    --card-dark: #2b2b2b;
    --silver: #9d9d9d;
    --silver-mid: #919191;
    --silver-light: #aaaaaa;
    --text-light: #e2e2e2;
    --icon-bg: #d6d6d6;
  }
  * { margin: 0; padding: 0; box-sizing: border-box; }
  html, body {
    width: 1200px;
    height: 902px;
    overflow: hidden;
    background: var(--page-bg);
    font-family: "Lato", Arial, sans-serif;
  }
  .canvas { position: relative; width: 1200px; height: 902px; }
  .business-card {
    position: absolute;
    left: 100px;
    top: 165px;
    width: 1000px;
    height: 572px;
    border-radius: 26px;
    overflow: hidden;
    background: var(--card-light);
    box-shadow: 0 6px 24px rgba(0,0,0,0.12);
  }
  .card-shapes { position: absolute; inset: 0; }
  .name-tab {
    position: absolute;
    left: -22px;
    top: 85px;
    width: 44px;
    height: 44px;
    border-radius: 50%;
    background: var(--icon-bg);
  }
  .holder-name {
    position: absolute;
    left: 54px;
    top: 86px;
    font-weight: 700;
    font-size: 33px;
    letter-spacing: 0.5px;
    color: var(--text-light);
    text-transform: uppercase;
  }
  .contact-block {
    position: absolute;
    left: 53px;
    top: 286px;
    color: var(--text-light);
    font-size: 25px;
    line-height: 34px;
  }
  .address { margin-bottom: 28px; }
  .contact-line { display: flex; align-items: center; gap: 12px; height: 40px; }
  .contact-icon {
    width: 28px; height: 28px;
    border-radius: 5px;
    background: var(--icon-bg);
    display: flex; align-items: center; justify-content: center;
  }
  .brand {
    position: absolute;
    left: 526px;
    top: 226px;
    display: flex;
    align-items: center;
    gap: 24px;
  }
  .brand-square {
    width: 84px; height: 84px;
    background: var(--silver-light);
  }
  .brand-name {
    font-weight: 900;
    font-size: 100px;
    line-height: 1;
    letter-spacing: 2px;
    color: var(--silver);
  }
</style>
</head>
<body>
<main class="canvas">
  <section class="business-card" aria-label="Visitenkarte KVTL">
    <svg class="card-shapes" width="1000" height="572" viewBox="0 0 1000 572" aria-hidden="true">
      <path d="M0 0 H516 Q 384 286 520 572 H0 Z" fill="var(--card-dark)"/>
      <path d="M524 0 Q 394 286 530 572 Q 414 286 524 0 Z" fill="var(--silver-light)"/>
    </svg>

    <span class="name-tab" aria-hidden="true"></span>
    <h1 class="holder-name">Lukas Brenner</h1>

    <div class="contact-block">
      <p class="address">Kellberger Str. 18<br>74286 Oberweiler</p>
      <p class="contact-line">
        <span class="contact-icon" aria-hidden="true">
          <svg width="18" height="18" viewBox="0 0 24 24"><path d="M6.6 10.8a15 15 0 0 0 6.6 6.6l2.2-2.2c.3-.3.7-.4 1-.2 1.1.4 2.3.6 3.6.6.6 0 1 .4 1 1V20c0 .6-.4 1-1 1C10.6 21 3 13.4 3 4c0-.6.4-1 1-1h3.5c.6 0 1 .4 1 1 0 1.3.2 2.5.6 3.6.1.3 0 .7-.2 1z" fill="var(--card-dark)"/></svg>
        </span>
        07146-839214-0
      </p>
      <p class="contact-line">
        <span class="contact-icon" aria-hidden="true">
          <svg width="18" height="14" viewBox="0 0 24 18"><rect x="1" y="1" width="22" height="16" rx="1.5" fill="none" stroke="var(--card-dark)" stroke-width="2"/><path d="M2 2l10 8 10-8" fill="none" stroke="var(--card-dark)" stroke-width="2"/></svg>
        </span>
        Name@agentur-kvtl.de
      </p>
    </div>

    <div class="brand">
      <span class="brand-square" aria-hidden="true"></span>
      <span class="brand-name">KVTL</span>
    </div>
  </section>
</main>
</body>
</html>
```